Revise our price listr for 2023

Please see attached price list with new prices to revise.
Please include new logo
Please add the text: Please note that prices are subject to change without prior notice.
Please remove prices from equipment with operator
Please add Under Commercial stone:
Fill Dirt $16.
Please add under Decorative Stone:
3/4" Barn Red Stone $127.
3/4" Yellow Ocean Gravel $140.
3/4" Delaware River Gravel $110.
1" Nutmeg Pebble $97.
Price list sending via email and customer in our lobby
Landscape and construction supply

```html
<!DOCTYPE html>
<html lang="en">
<head>
<meta charset="utf-8">
<title>Ridgeline Supply – 2023 Material Price List</title>
<link href="https://fonts.googleapis.com/css2?family=Poppins:wght@400;500;600;700&family=Oswald:wght@300;700&display=swap" rel="stylesheet">
<style>
  :root{
    --green:#1c9a46;
    --green-dark:#137a35;
    --maroon:#6e1515;
    --maroon-dark:#561010;
    --ink:#1d1d1d;
    --paper:#ffffff;
    --canvas:#eeeeee;
    --leader:#9a9a9a;
  }
  *{box-sizing:border-box;margin:0;padding:0}
  html,body{width:783px;height:1200px;overflow:hidden;background:var(--canvas)}
  body{font-family:"Poppins",sans-serif;color:var(--ink);position:relative}

  .price-sheet{position:absolute;left:12px;top:306px;width:760px;height:588px;
    background:linear-gradient(180deg,var(--green) 0%,#22a84f 50%,var(--maroon) 50%,var(--maroon-dark) 100%)}
  .sheet-panel{position:absolute;left:13px;top:10px;right:12px;bottom:11px;background:var(--paper);
    border-radius:34px 0 34px 0}

  .col{position:absolute;top:0}
  .col-left{left:26px;width:200px}
  .col-mid{left:259px;width:211px}
  .col-right{left:506px;width:208px}

  /* brand */
  .brand{margin-top:24px;height:52px;display:flex;align-items:center;justify-content:center;gap:6px}
  .brand-dot{width:14px;height:14px;border-radius:50%;background:var(--green)}
  .brand-name{font-weight:700;font-size:17px;color:var(--maroon);letter-spacing:.3px}

  /* ribbons */
  .ribbon{background:var(--maroon);color:#fff;font-weight:700;text-align:center;
    clip-path:polygon(0 0,100% 0,96% 50%,100% 100%,0 100%,4% 50%);
    margin:0 auto;width:172px;font-size:12px;line-height:19px;text-transform:uppercase}

  /* price rows */
  .price-list{list-style:none;margin-top:6px}
  .price-row{display:flex;align-items:center;height:13px;font-size:8.6px;white-space:nowrap}
  .price-row .leader{flex:1;border-bottom:1px dotted var(--leader);margin:0 3px;transform:translateY(1px)}
  .price-tag{width:29px;height:11px;background:var(--green);color:#fff;font-weight:600;font-size:7px;
    text-align:center;line-height:11px;clip-path:polygon(0 0,100% 0,100% 100%,0 100%,14% 50%);padding-left:3px;flex:none}
  .price-tag.call{font-size:6px}
  .price-tag.small{font-size:6px}

  .left-soil{margin-top:8px}
  .gap-sect{margin-top:9px}

  .feature-box{margin:10px 0 0 0;border:1px solid #cfcfcf;height:68px;position:relative;padding:8px 40px 0 12px}
  .feature-box::after{content:"";position:absolute;right:0;top:0;width:38px;height:100%;background:var(--green)}
  .feature-box .price-row{position:relative}
  .feature-box .price-row .value{position:absolute;right:-36px;width:32px;text-align:center;color:#fff;font-weight:600;font-size:8px;z-index:1}

  /* title */
  .sheet-title{text-align:center;margin-top:12px;color:var(--maroon);font-family:"Oswald",sans-serif;font-size:0;white-space:nowrap}
  .sheet-title .year-line{display:block;font-size:28px;line-height:32px;color:var(--green);font-weight:300}
  .sheet-title .year-line b{font-weight:700}
  .sheet-title .main-line{display:block;font-size:46px;line-height:50px;font-weight:700;letter-spacing:-1px}

  .note-row{display:flex;align-items:center;height:13px;font-size:8.6px;white-space:nowrap}
  .note-row .leader{flex:1;border-bottom:1px dotted var(--leader);margin:0 4px;transform:translateY(1px)}
  .call-quote{color:var(--maroon);font-weight:700;font-size:7.5px}

  .radius-box{margin:8px auto 0;width:206px;height:40px;background:var(--maroon);padding:3px}
  .radius-box div{border:1px solid #fff;height:100%;color:#fff;font-size:9.5px;line-height:12px;text-align:center;
    display:flex;align-items:center;justify-content:center}

  .photo-strip{position:absolute;left:268px;top:456px;width:440px;height:70px;display:flex;gap:12px}
  .photo{flex:1;transform:skewX(-10deg);border:3px solid #fff;box-shadow:0 1px 3px rgba(0,0,0,.3)}
  .photo-limestone{background:linear-gradient(135deg,#d8d2c6,#a59d90)}
  .photo-basalt{background:linear-gradient(135deg,#6c6c6c,#2f2f2f)}
  .photo-river{background:linear-gradient(135deg,#c79b77,#8a7d6e)}
  .price-note{position:absolute;left:258px;top:536px;width:460px;text-align:center;font-size:11.5px;line-height:16px}

  /* right column */
  .equip-ribbon{margin:18px auto 0;width:172px;background:var(--maroon);color:#fff;font-weight:700;
    font-size:11.5px;line-height:13px;text-align:center;padding:4px 0;
    clip-path:polygon(0 0,100% 0,96% 50%,100% 100%,0 100%,4% 50%)}
  .call-pill{margin:4px auto 0;width:156px;height:18px;border-radius:9px;background:var(--green);color:#fff;
    font-weight:700;font-size:11.5px;line-height:18px;text-align:center}
  .equip-group{border-bottom:1px dotted var(--leader);padding:6px 0}
  .equip-group:last-of-type{border-bottom:none}
  .equip-head{color:var(--green);font-weight:700;font-size:8.2px;line-height:12px}
  .equip-grid{display:grid;grid-template-columns:1fr .88fr;font-size:8.6px;line-height:13px}
  .equip-line{font-size:8.6px;line-height:10.5px}
  .equip-calls .price-row{height:12.5px}

  .know-box{position:absolute;left:506px;top:364px;width:203px;height:74px}
  .know-pill{position:absolute;left:40px;top:0;width:138px;height:17px;border-radius:9px;background:var(--maroon);
    color:#fff;font-weight:700;font-size:11.5px;line-height:17px;text-align:center;z-index:2}
  .know-bulb{position:absolute;left:30px;top:-6px;width:14px;height:14px;border-radius:50%;background:#f2b631;z-index:3}
  .know-green{position:absolute;top:9px;left:0;right:0;height:35px;background:var(--green);color:#fff;
    font-size:8px;line-height:10px;text-align:center;padding-top:11px}
  .know-maroon{position:absolute;top:44px;left:0;right:0;height:30px;background:var(--maroon);color:#fff;
    font-weight:700;font-size:7.6px;line-height:10px;text-align:center;padding-top:5px}
</style>
</head>
<body>
<div class="price-sheet">
  <div class="sheet-panel">

    <section class="col col-left">
      <div class="brand"><span class="brand-dot"></span><span class="brand-name">RIDGELINE SUPPLY</span></div>

      <h2 class="ribbon left-soil">Soil</h2>
      <ul class="price-list">
        <li class="price-row">Sandy Loam<span class="leader"></span><span class="price-tag">$30</span></li>
        <li class="price-row">Topsoil-Screened<span class="leader"></span><span class="price-tag">$42</span></li>
        <li class="price-row">Garden Soil<span class="leader"></span><span class="price-tag">$52</span></li>
        <li class="price-row">Mushroom Dirt<span class="leader"></span><span class="price-tag">$55</span></li>
        <li class="price-row">Compost (Leaf &amp; Grass)<span class="leader"></span><span class="price-tag">$55</span></li>
      </ul>

      <h2 class="ribbon gap-sect">Mulch</h2>
      <ul class="price-list">
        <li class="price-row">Mulch-Dyed Black<span class="leader"></span><span class="price-tag">$42</span></li>
        <li class="price-row">Mulch-Dyed Red<span class="leader"></span><span class="price-tag">$42</span></li>
        <li class="price-row">Mulch-Dyed Brown<span class="leader"></span><span class="price-tag">$42</span></li>
        <li class="price-row">Mulch-Natural Light Brown<span class="leader"></span><span class="price-tag">$38</span></li>
        <li class="price-row">Mulch-Dark Triple Ground<span class="leader"></span><span class="price-tag">$44</span></li>
        <li class="price-row">Mulch Cedar<span class="leader"></span><span class="price-tag">$55</span></li>
      </ul>

      <h2 class="ribbon gap-sect">Decorative Stone</h2>
      <ul class="price-list">
        <li class="price-row">White Limestone #1 [1/4*-1/2"]<span class="leader"></span><span class="price-tag">$95</span></li>
        <li class="price-row">White Limestone #2 [1/2*-3/4"*}<span class="leader"></span><span class="price-tag small">$97.50</span></li>
        <li class="price-row">River Rock #2 [3/4*] Round<span class="leader"></span><span class="price-tag">$50</span></li>
        <li class="price-row">River Rock-Medium [2/37]<span class="leader"></span><span class="price-tag">$95</span></li>
        <li class="price-row">River Rounds [4-6*)<span class="leader"></span><span class="price-tag">$90</span></li>
        <li class="price-row">Pea Gravel<span class="leader"></span><span class="price-tag">$50</span></li>
        <li class="price-row">Berkshire Blend<span class="leader"></span><span class="price-tag">$120</span></li>
      </ul>

      <ul class="price-list feature-box">
        <li class="price-row">3/4" Barn Red Stone<span class="leader"></span><span class="value">$127</span></li>
        <li class="price-row">3/4" Yellow Ocean Gravel<span class="leader"></span><span class="value">$140</span></li>
        <li class="price-row">3/4" Delaware River Gravel<span class="leader"></span><span class="value">$110</span></li>
        <li class="price-row">1" Nutmeg Pebble<span class="leader"></span><span class="value">$97</span></li>
      </ul>

      <h2 class="ribbon" style="margin-top:10px">Sand</h2>
      <ul class="price-list">
        <li class="price-row">Masonary/Pool Sand<span class="leader" style="border:none"></span><span class="price-tag">$45</span></li>
        <li class="price-row">Bedding Sand<span class="leader" style="border:none"></span><span class="price-tag">$37</span></li>
      </ul>
    </section>

    <section class="col col-mid">
      <h1 class="sheet-title"><span class="year-line">2023 <b>MATERIAL</b></span><span class="main-line">PRICE LIST</span></h1>

      <h2 class="ribbon" style="margin-top:4px">Commercial Stone</h2>
      <ul class="price-list" style="margin-top:8px">
        <li class="price-row">Item #4<span class="leader"></span><span class="price-tag">$42</span></li>
        <li class="price-row">#1 Stome (1/2")<span class="leader"></span><span class="price-tag">$45</span></li>
        <li class="price-row">#2 Stone (3/4* 1")<span class="leader"></span><span class="price-tag">$45</span></li>
        <li class="price-row">3 (1.5* 2*)<span class="leader"></span><span class="price-tag">$45</span></li>
        <li class="price-row">Stone Chip (fine)<span class="leader"></span><span class="price-tag">$40</span></li>
        <li class="price-row">Stone Dust (xtra fine)<span class="leader"></span><span class="price-tag">$47</span></li>
        <li class="price-row">Shale When Available<span class="leader" style="border:none"></span><span class="price-tag call">CALL</span></li>
        <li class="price-row">Bank Run Fill (Dirt &amp; Cobble)<span class="leader"></span><span class="price-tag">$18</span></li>
        <li class="price-row">Crusher RUDe<span class="leader" style="border:none"></span><span class="price-tag">$42</span></li>
        <li class="price-row">Fill Dirt<span class="leader"></span><span class="price-tag">$16</span></li>
      </ul>

      <h2 class="ribbon" style="margin-top:8px">Seasonal</h2>
      <ul class="price-list" style="margin-top:5px">
        <li class="price-row">Treated Salt Green<span class="leader"></span><span class="price-tag">$165</span></li>
      </ul>

      <h2 class="ribbon" style="margin-top:5px">Delivery Charges</h2>
      <ul class="price-list" style="margin-top:6px">
        <li class="price-row">Local (Small Truck)<span class="leader"></span><span class="price-tag">$60</span></li>
        <li class="price-row">Local (Medium Truck)<span class="leader"></span><span class="price-tag">$75</span></li>
        <li class="price-row">Local (Large Truck)<span class="leader"></span><span class="price-tag">$115</span></li>
        <li class="note-row">Non Local<span class="leader"></span><span class="call-quote">CALL FOR QUOTE</span></li>
      </ul>

      <div class="radius-box"><div>Local deliverys 7 mile radius<br>excluding the mat</div></div>
    </section>

    <section class="col col-right">
      <h2 class="equip-ribbon">EQUIPMENT WITH<br>OPERATOR AVAILABLE</h2>
      <div class="call-pill">CALL FOR PRICING</div>

      <div class="equip-group" style="margin-top:4px">
        <div class="equip-grid"><span>Onsite Mobile</span><span>Forestry</span><span>Grinding/Tub Grinding</span><span>Mulching</span></div>
      </div>
      <div class="equip-group">
        <div class="equip-head">Skid Steer: (Rubber Track)</div>
        <div class="equip-grid"><span>Available Attachment</span><span>3/4 Yard Bucket</span><span>Harley Rake</span><span>Hydraulic Auger</span><span>Forestry Mulching</span><span>Grapple Bucket</span></div>
      </div>
      <div class="equip-group">
        <div class="equip-head">EXCAVATOR</div>
        <div class="equip-grid"><span>35 Class (7,500bs)</span><span>[60 Class (38,500bs)</span><span>90 Class (14,000bs)</span><span>50 Class (60,000bs)</span><span>L40 Class (45,500bs)</span><span></span></div>
      </div>
      <div class="equip-group">
        <div class="equip-head">BULL DOZER</div>
        <div class="equip-grid"><span>450 Class (18,000bs)</span><span>Vibratory Roller</span><span>700 Class (30,000bs)</span><span>Rock Hammer</span></div>
        <p class="equip-line" style="margin-top:4px">Hydraulic Rock Hammer on 160 Class excavator.<br>Additional mobilization fee for 1st day</p>
        <ul class="price-list equip-calls" style="margin-top:2px">
          <li class="price-row">Tri-Axle Dump<span class="leader" style="border:none"></span><span class="price-tag call">CALL</span></li>
          <li class="price-row">Dump Trailer<span class="leader"></span><span class="price-tag call">CALL</span></li>
        </ul>
      </div>
    </section>

    <div class="know-box">
      <span class="know-bulb"></span>
      <div class="know-pill">DID YOU KNOW?</div>
      <div class="know-green">We Offer Onside Tub Grinding &amp;<br>We are a GREEN RECYCLING Location!</div>
      <div class="know-maroon">NON LOCAL CALL FOR PRICING<br>ALSO THANK YOU</div>
    </div>

    <div class="photo-strip">
      <div class="photo photo-limestone" role="img" aria-label="Photo of white limestone gravel"></div>
      <div class="photo photo-basalt" role="img" aria-label="Photo of dark grey crushed stone"></div>
      <div class="photo photo-river" role="img" aria-label="Photo of colourful river rock pebbles"></div>
    </div>

    <p class="price-note">Please note that prices are subject to change without prior notice.</p>
  </div>
</div>
</body>
</html>
```